Local Roofing/Construction company business needs new biz card design

We need a new business card design, current cards are from the start of this operation and generic at best. We are a local Construction Company (General Contractor) with a majority of our work originating from insurance claims-exterior finish work is the main focus (Roofs-Siding-Gutters etc). Heavily involved with homeowners and the low ball offers they receive from insurance company's after a insurable event takes place. I have attached some of our original logo file(s) below.

```html
<!DOCTYPE html>
<html lang="en">
<head>
<meta charset="utf-8">
<title>Stonebridge Builders – Business Card</title>
<link href="https://fonts.googleapis.com/css2?family=Lato:wght@400;700;900&display=swap" rel="stylesheet">
<style>
  :root {
    --stage: #3b3c3f;
    --ink: #0f1e1f;
    --ink-soft: #16292a;
    --green: #2fd27a;
    --paper: #ffffff;
    --grey: #6b6f70;
  }
  * { box-sizing: border-box; margin: 0; padding: 0; }
  html, body { width: 1200px; height: 952px; overflow: hidden; }
  body {
    background: var(--stage);
    font-family: "Lato", sans-serif;
    position: relative;
  }
  .card {
    position: absolute;
    left: 280px;
    width: 640px;
    height: 366px;
    border-radius: 28px;
    overflow: hidden;
  }
  .card--front { top: 80px; background: var(--paper); }
  .card--back { top: 500px; background: var(--ink); }

  .brand {
    position: absolute;
    top: 34px;
    right: 40px;
    display: flex;
    align-items: center;
    gap: 14px;
    background: var(--ink);
    border-radius: 14px;
    padding: 18px 26px;
  }
  .brand__mark { width: 34px; height: 34px; background: var(--green); border-radius: 4px; }
  .brand__name {
    color: var(--paper);
    font-weight: 900;
    font-size: 28px;
    letter-spacing: 1px;
    text-transform: uppercase;
    line-height: 1;
  }

  .person { position: absolute; left: 40px; top: 160px; }
  .person__name {
    font-size: 24px;
    color: var(--ink);
    text-transform: uppercase;
    letter-spacing: 0.5px;
  }
  .person__name strong { color: var(--green); font-weight: 900; }
  .person__role { margin-top: 6px; font-size: 17px; color: var(--grey); }

  .contacts {
    position: absolute;
    left: 330px;
    top: 150px;
    list-style: none;
    display: flex;
    flex-direction: column;
    gap: 10px;
  }
  .contacts li {
    display: flex;
    align-items: center;
    gap: 10px;
    font-size: 16px;
    color: var(--ink);
  }
  .contacts svg { width: 22px; height: 22px; flex: none; }

  .address-band {
    position: absolute;
    left: 0; right: 0;
    top: 276px;
    height: 40px;
    background: var(--ink);
    color: var(--paper);
    font-size: 16px;
    display: flex;
    align-items: center;
    padding-left: 40px;
    letter-spacing: 0.3px;
  }

  .back-pattern {
    position: absolute;
    inset: 0;
    background: linear-gradient(135deg, var(--ink-soft), var(--ink));
  }
  .back-brand {
    position: absolute;
    right: 40px;
    bottom: 40px;
    display: flex;
    align-items: center;
    gap: 10px;
  }
  .back-brand__mark { width: 22px; height: 22px; background: var(--green); border-radius: 3px; }
  .back-brand__name {
    color: var(--green);
    font-weight: 900;
    font-size: 18px;
    text-transform: uppercase;
    letter-spacing: 1px;
  }
</style>
</head>
<body>

<section class="card card--front">
  <div class="brand">
    <span class="brand__mark"></span>
    <span class="brand__name">Stonebridge Builders</span>
  </div>

  <div class="person">
    <p class="person__name">Daniel M. <strong>Foster</strong></p>
    <p class="person__role">General Contractor</p>
  </div>

  <ul class="contacts">
    <li>
      <svg viewBox="0 0 22 22"><rect width="22" height="22" rx="4" fill="var(--ink)"/><path d="M7 5.5c.8-.5 1.6 0 2 .8l.8 1.7c.3.6 0 1.2-.5 1.5l-.6.4c.5 1.3 1.5 2.4 2.8 3l.4-.6c.4-.5 1-.7 1.5-.4l1.7.8c.8.4 1.2 1.3.7 2-.7 1.1-2 1.6-3.3 1.1C9.600 14.800 7.300 12.500 6.300 9.600 5.800 8.100 6.100 6.200 7 5.500z" fill="#fff"/></svg>
      +00 123 456 78
    </li>
    <li>
      <svg viewBox="0 0 22 22"><rect width="22" height="22" rx="4" fill="var(--ink)"/><rect x="5" y="7" width="12" height="8.5" rx="1" fill="none" stroke="#fff" stroke-width="1.4"/><path d="M5.5 7.5 11 12l5.5-4.5" fill="none" stroke="#fff" stroke-width="1.4"/></svg>
      companyname@mail.com
    </li>
    <li>
      <svg viewBox="0 0 22 22"><rect width="22" height="22" rx="4" fill="var(--ink)"/><path d="M11 5 16 11h-3v6H9v-6H6z" fill="#fff"/></svg>
      www.companywebsite.com
    </li>
  </ul>

  <div class="address-band">2417 Harbor Lane Springfield, DC 20031</div>
</section>

<section class="card card--back">
  <div class="back-pattern" role="img" aria-label="Faint repeating pattern of the company mark across a dark teal background"></div>
  <div class="back-brand">
    <span class="back-brand__mark"></span>
    <span class="back-brand__name">Stonebridge Builders</span>
  </div>
</section>

</body>
</html>
```